Holiday Rental Company Flyer Design (DL not A5)

Note from Brandloom Administration: The category sizing selected is A5, however the project requires DL sized artwork. Please refer to the DL template link below while the 'Special Requirements' are updated accordingly.

Project Brief:
We need a double sided DL flyer designed for an up market Holiday Rental Company that portrays a personalised approach to property management. These are to be used for letter box drops to homes we're specifically targeting so the design should be modern, complimentary colour palette, uncluttered & visually appealing.

Please Download the DL Template from Quillora here: http://www.quillora.com.au/ql/ns/propath/UploadResources.aspx?selectedTab=0?pfid=KMT&pf_id=KMT&xnav=easypath-upload-image#Templates

Target Market(s)

Wealthy Home Owners

Industry/Entity Type

It Company

Other font styles liked:
• Avant Garde Extra Light & Demi

Colors
33b8a4

Requirements
Must have
• DL Flyer sizes (210mm width x 99mm width, plus 3mm bleed)
• Front: Logo, Main Image & Grab
• Back: Contact Details & Brief Description of our business
• Images: Ideally the main image should be the house with the pool but alternatively a lifestyle images could also be used.
Nice to have
• A creative designer!
Should not have
• Clutter & busy designs

```html
<!DOCTYPE html>
<html lang="en">
<head>
<meta charset="utf-8">
<title>Harbourline Stays – DL Flyer</title>
<link rel="stylesheet" href="https://fonts.googleapis.com/css2?family=Poppins:wght@500;600&family=Questrial&display=swap">
<style>
  :root {
    --canvas: #ffffff;
    --brand-green: #4faa8c;
    --panel-green: rgba(93, 178, 142, 0.82);
    --panel-green-inner: rgba(118, 190, 160, 0.9);
    --body-grey: #6a6a6a;
    --white: #ffffff;
    --night-top: #1c1f2e;
    --night-mid: #4b3f63;
    --pool-blue: #3f7fc4;
    --sea-top: #eef1f2;
    --sea-bottom: #d9e3e8;
  }
  * { margin: 0; padding: 0; box-sizing: border-box; }
  html, body { width: 1200px; height: 971px; overflow: hidden; background: var(--canvas); }
  .canvas { position: relative; width: 1200px; height: 971px; }

  /* Front side */
  .front { position: absolute; left: 100px; top: 0; width: 465px; height: 971px; overflow: hidden; }
  .front-photo {
    position: absolute; inset: 0;
    background:
      linear-gradient(180deg, transparent 60%, var(--pool-blue) 78%, #6fa9df 100%),
      linear-gradient(120deg, var(--night-top) 0%, #3a3240 30%, #7a6a8a 55%, var(--night-mid) 70%, #c9a56a 85%, #2a2a35 100%);
  }
  .front-headline {
    position: absolute; left: 0; width: 465px; top: 118px;
    font-family: "Poppins", sans-serif; font-weight: 600;
    font-size: 44px; line-height: 57.5px; color: var(--white);
    text-align: center; letter-spacing: -0.5px;
  }
  .brand-panel { position: absolute; left: 80px; top: 582px; width: 303px; height: 389px; background: var(--panel-green); }
  .brand-panel-inner { position: absolute; left: 12px; top: 15px; width: 279px; height: 374px; background: var(--panel-green-inner); }
  .brand-mark { position: absolute; left: 89px; top: 70px; width: 100px; height: 100px; border: 2px solid var(--white); border-radius: 50%; }
  .brand-name {
    position: absolute; left: 0; width: 279px; top: 220px;
    font-family: "Questrial", sans-serif; font-size: 36px; line-height: 42px;
    letter-spacing: 3px; color: var(--white); text-align: center;
  }

  /* Back side */
  .back { position: absolute; left: 655px; top: 0; width: 465px; height: 971px; overflow: hidden; }
  .back-photo { position: absolute; inset: 0; background: linear-gradient(180deg, var(--sea-top) 0%, #f3f5f6 40%, var(--sea-bottom) 100%); }
  .story-frame {
    position: absolute; left: 42px; top: 70px; width: 381px; height: 720px;
    border: 2px solid var(--brand-green); border-top: none;
  }
  .story-frame::before, .story-frame::after {
    content: ""; position: absolute; top: 0; height: 2px; width: 20px; background: var(--brand-green);
  }
  .story-frame::before { left: -2px; }
  .story-frame::after { right: -2px; }
  .story-heading {
    position: absolute; left: 0; width: 465px; top: 52px;
    font-family: "Poppins", sans-serif; font-weight: 600; font-size: 25px;
    color: var(--brand-green); text-align: center; line-height: 36px;
  }
  .story-copy {
    position: absolute; left: 50px; width: 365px; top: 141px;
    font-family: "Questrial", sans-serif; font-size: 19.5px; line-height: 25px;
    color: var(--body-grey); text-align: center;
  }
  .story-copy p + p { margin-top: 25px; }
  .edge-band { position: absolute; top: 790px; width: 20px; height: 181px; background: rgba(79, 170, 140, 0.18); }
  .edge-band.left { left: 61px; }
  .edge-band.right { left: 382px; }
  .contact-panel { position: absolute; left: 80px; top: 582px; width: 303px; height: 389px; background: var(--panel-green); }
  .contact-panel-inner { position: absolute; left: 10px; top: 15px; width: 283px; height: 374px; background: var(--panel-green-inner); }
  .contact-invite {
    position: absolute; left: 0; width: 283px; top: 14px;
    font-family: "Questrial", sans-serif; font-size: 21px; line-height: 27px;
    color: var(--white); text-align: center;
  }
  .contact-details {
    position: absolute; left: 0; width: 283px; top: 210px;
    font-family: "Poppins", sans-serif; font-weight: 600; font-size: 12.5px; line-height: 19.5px;
    color: var(--white); text-align: center;
  }
</style>
</head>
<body>
<main class="canvas">
  <section class="front">
    <div class="front-photo" role="img" aria-label="Modern luxury house at dusk with lit windows and a blue swimming pool"></div>
    <h1 class="front-headline">Holiday<br>Rental<br>Management<br>with<br>a<br>difference</h1>
    <div class="brand-panel">
      <div class="brand-panel-inner">
        <span class="brand-mark"></span>
        <p class="brand-name">HARBOURLINE<br>STAYS</p>
      </div>
    </div>
  </section>

  <section class="back">
    <div class="back-photo" role="img" aria-label="Faint calm sea with a moored fishing boat"></div>
    <div class="story-frame"></div>
    <h2 class="story-heading">What we do differently!</h2>
    <div class="story-copy">
      <p>Rather than relying upon a key safe<br>or a central pick-up destination, a<br>‘Harbourline Stays’ staff member<br>will greet guests upon arrival.</p>
      <p>Our ‘Meet &amp; Greet’ service provides<br>home owners with an increased<br>level of Security and also allows us<br>to:<br>Prepare the home for their arrival<br>(lights, heaters, music etc.)<br>Establish a rapport &amp; help facilitate<br>future bookings<br>Reiterate their responsibilities to<br>ensure the return of their bond</p>
    </div>
    <div class="edge-band left" role="img" aria-label="Decorative pattern strip"></div>
    <div class="edge-band right" role="img" aria-label="Decorative pattern strip"></div>
    <div class="contact-panel">
      <div class="contact-panel-inner">
        <p class="contact-invite">If you’d like to know<br>what your property<br>could achieve or<br>require additional<br>information, please<br>contact us on:</p>
        <p class="contact-details">t: (03)5900 2417<br>e: stay@harbourlinestays.com.au<br>w: harbourlinestays.com.au<br>PO Box 48, Coralvale Victoria 3999</p>
      </div>
    </div>
  </section>
</main>
</body>
</html>
```